Develop website for Cloud Security Startup

Looking for a logo that conveys the outsourced security and management of clients data, systems and development in Tellix, Bri and Pindle with an emphasis on security and compliance

Target Market(s)

Companies looking for professional services IT firm

Coding

Coded - Design and coding required

Number of Pages Required

5+ page

Font styles to use
Sans Serif

Colors
0455a3
33a6d7

Requirements
Must have
• Landing Page
- Help me get started

Move to the cloud safely
- Benefits of Cloud

What we do
- Cloud Adoption
- Managed Services
- Optimise

Resources
- News
- Resources
- Events
- Webinars
- Not for profit
- Case Studies
- Support Button
- Incident Button

Company
- About Us
- Why Vorplexa?
- Acreditations
- Quorvane Tellix Partner
- Net Promoter Score
- Careers
- Contact Us

Contact Us

```html
<!DOCTYPE html>
<html lang="en">
<head>
<meta charset="utf-8">
<title>Vorplexa – Effective Technology Management</title>
<link href="https://fonts.googleapis.com/css2?family=Montserrat:wght@400;500;600;700&display=swap" rel="stylesheet">
<style>
:root{
  --navy:#0a3f94;
  --blue:#0455a3;
  --deep:#0b2a9c;
  --sky:#33a6d7;
  --ink:#333;
  --muted:#555;
  --light:#f4f4f4;
  --white:#fff;
}
*{margin:0;padding:0;box-sizing:border-box}
html,body{width:1200px;height:3479px;overflow:hidden}
body{position:relative;font-family:Arial,Helvetica,sans-serif;color:var(--ink);background:var(--white)}
.abs{position:absolute}
.mont{font-family:'Montserrat',sans-serif}

/* header */
.header{left:0;top:0;width:1200px;height:154px;background:var(--white)}
.brand{display:flex;align-items:center;gap:10px}
.brand-dot{width:34px;height:34px;border-radius:50%;background:var(--blue)}
.brand-name{font-family:'Montserrat',sans-serif;font-weight:700;font-size:30px;color:var(--blue);letter-spacing:1px}
.brand-tag{font-family:'Montserrat',sans-serif;font-size:9px;color:var(--blue);letter-spacing:.3px;margin-top:2px}
.call{right:108px;top:22px;display:flex;align-items:center;gap:10px;font-family:'Montserrat',sans-serif;font-weight:600;font-size:18px;color:var(--blue)}
.call-ico{width:62px;height:62px;border-radius:50%;background:var(--blue);display:flex;align-items:center;justify-content:center}
.nav{right:110px;top:106px;display:flex;gap:30px;font-family:'Montserrat',sans-serif;font-weight:500;font-size:14px;color:#222}
.nav .on{color:var(--blue)}

/* hero */
.hero{left:0;top:154px;width:1200px;height:722px;background:linear-gradient(90deg,#091a6e 0%,#0c2eb0 55%,#0a1f8a 100%)}
.hero-art{left:40px;top:110px;width:660px;height:540px;border-radius:40px;background:radial-gradient(ellipse at 40% 40%,#2f8df0 0%,#1546c8 45%,rgba(12,46,176,0) 75%)}
.hero-title{left:715px;top:400px;font-family:'Montserrat',sans-serif;font-weight:600;font-size:54px;color:var(--white);letter-spacing:1px}
.hero-sub{left:719px;top:484px;font-family:'Montserrat',sans-serif;font-weight:600;font-size:15px;line-height:33px;color:var(--white)}
.btn{display:flex;align-items:center;justify-content:center;border-radius:30px;font-family:'Montserrat',sans-serif;font-weight:600}
.hero-btn{left:717px;top:572px;width:224px;height:56px;background:var(--sky);color:var(--white);font-size:15px}

/* section titles */
.sec-title{left:0;width:1200px;text-align:center;font-family:'Montserrat',sans-serif;font-weight:600;font-size:32px}
.rule{width:50px;height:3px;left:575px}

/* services */
.service{width:340px;text-align:center}
.pin{width:155px;height:190px;margin:0 auto}
.service h3{font-family:'Montserrat',sans-serif;font-weight:500;font-size:22px;color:#333;margin-top:18px}
.service p{font-size:14px;line-height:26px;color:var(--muted);margin-top:12px}
.outline-btn{width:146px;height:50px;margin:22px auto 0;border:2px solid var(--blue);color:#333;font-size:15px}

/* resources */
.resources{left:0;top:1497px;width:1200px;height:671px;background:linear-gradient(180deg,#3aa3dc 0%,#2a86cc 100%)}
.res-text{left:0;top:1623px;width:1200px;text-align:center;color:var(--white);font-size:14px;line-height:26px}
.card{width:150px;height:148px;background:var(--white);border-radius:8px;display:flex;flex-direction:column;align-items:center;justify-content:flex-end;padding-bottom:22px;gap:16px;font-family:'Montserrat',sans-serif;font-weight:500;font-size:17px;color:#222}
.support{left:397px;top:1995px;width:198px;height:62px;background:#0b3a9a;color:var(--white);font-size:18px;font-weight:500}
.incident{left:603px;top:1995px;width:198px;height:62px;border:2px solid var(--white);color:var(--white);font-size:18px;font-weight:500}

/* why */
.why-title{left:111px;top:2272px;font-family:'Montserrat',sans-serif;font-weight:700;font-size:37px;color:var(--blue)}
.why-title span{color:var(--sky)}
.why-block{left:111px;top:2352px;width:402px;display:flex;flex-direction:column}
.why-text{font-size:13.4px;line-height:26px;color:var(--muted);text-align:justify}
.why-btn{margin-top:28px;width:178px;height:58px;background:var(--blue);color:var(--white);font-size:16px}
.why-art{left:560px;top:2240px;width:640px;height:380px;background:radial-gradient(ellipse at 55% 65%,#d6f0fb 0%,#e9f7fd 45%,rgba(255,255,255,0) 75%)}

/* partner */
.partner{left:0;top:2709px;width:1200px;height:391px;background:var(--light)}
.badge{left:160px;top:2772px;width:254px;height:254px;border-radius:50%;background:var(--white);border-right:2px solid var(--sky);border-bottom:2px solid var(--sky)}
.badge-mark{left:235px;top:2880px;width:104px;height:38px;border-radius:6px;background:#cfe7f6}
.partner-title{left:478px;top:2818px;font-family:'Montserrat',sans-serif;font-weight:600;font-size:22px;color:var(--blue)}
.partner-text{left:480px;top:2871px;width:560px;font-size:14px;line-height:26px;color:var(--muted)}
.partner-btn{left:478px;top:2970px;width:155px;height:52px;background:var(--sky);color:var(--white);font-size:15px;font-weight:500}

/* footer */
.footer{left:0;top:3100px;width:1200px;height:379px;background:var(--navy);color:var(--white);font-family:'Montserrat',sans-serif}
.f-brand{left:160px;top:3180px;display:flex;flex-direction:column;align-items:center}
.f-dot{width:70px;height:70px;border-radius:50%;background:var(--white);margin-bottom:12px}
.f-name{font-weight:700;font-size:34px;letter-spacing:1px}
.f-tag{font-size:10px}
.divider{width:1px;height:122px;background:rgba(255,255,255,.35);top:3163px}
.f-info{font-size:16px;line-height:23px;font-weight:500}
.social{width:42px;height:42px;border-radius:50%;border:2px solid var(--white)}
.f-rule{left:110px;top:3370px;width:980px;height:1px;background:rgba(255,255,255,.2)}
.f-nav{left:0;top:3387px;width:1200px;display:flex;justify-content:center;gap:30px;font-size:14px;font-weight:500}
.copy{left:0;top:3432px;width:1200px;text-align:center;font-size:16px}
</style>
</head>
<body>

<header class="abs header">
  <div class="abs" style="left:111px;top:60px">
    <div class="brand"><div class="brand-dot"></div><div><div class="brand-name">VORPLEXA</div><div class="brand-tag">EFFECTIVE TECHNOLOGY MANAGEMENT</div></div></div>
  </div>
  <div class="abs call">
    <div class="call-ico"><svg width="20" height="20" viewBox="0 0 24 24" fill="#fff"><path d="M6.6 10.8a15 15 0 006.6 6.6l2.2-2.2a1 1 0 011-.25 11.4 11.4 0 003.6.57 1 1 0 011 1V20a1 1 0 01-1 1A17 17 0 013 4a1 1 0 011-1h3.5a1 1 0 011 1c0 1.25.2 2.45.57 3.6a1 1 0 01-.25 1z"/></svg></div>
    CALL US : 000-555-0142
  </div>
  <nav class="abs nav"><span class="on">HOME</span><span>CLOUD SAFELY</span><span>WHAT WE DO</span><span>RESOURCES</span><span>COMPANY</span><span>CONTACT US</span></nav>
</header>

<section class="abs hero">
  <div class="abs hero-art" role="img" aria-label="Isometric cloud server illustration glowing over a blue world map"></div>
</section>
<h1 class="abs hero-title">VORPLEXA</h1>
<p class="abs hero-sub">SED UT PERSPICIATIS UNDE OMNIS ISTE NATUS<br>ERROR SIT VOLUPTATEM ACCUSANTIUM</p>
<div class="abs btn hero-btn">HELP ME GET STARTED</div>

<h2 class="abs sec-title" style="top:928px;color:#333">WHAT WE DO</h2>
<div class="abs rule" style="top:977px;background:var(--blue)"></div>

<div class="abs service" style="left:93px;top:1035px">
  <svg class="pin" viewBox="0 0 155 190"><defs><linearGradient id="pg" x1="0" y1="0" x2="0" y2="1"><stop offset="0" stop-color="#1e7fd6"/><stop offset="1" stop-color="#0a3f94"/></linearGradient></defs><path d="M77.5 0A77.5 77.5 0 0 1 132 132L77.5 188 23 132A77.5 77.5 0 0 1 77.5 0z" fill="url(#pg)"/><g fill="none" stroke="#fff" stroke-width="3"><path d="M50 88a16 16 0 0 1 6-30 22 22 0 0 1 43 4 14 14 0 0 1 4 26"/><path d="M77 70v45M66 80v22h-8M88 80v22h8"/><circle cx="55" cy="102" r="4"/><circle cx="100" cy="102" r="4"/></g></svg>
  <h3>CLOUD ADOPTION</h3>
  <p>Sed ut perspiciatis unde omnis iste natus<br>error sit voluptatem accusantium dolorem<br>laudantium, totam rem aperiam</p>
  <div class="btn outline-btn">READ MORE</div>
</div>
<div class="abs service" style="left:429px;top:1035px">
  <svg class="pin" viewBox="0 0 155 190"><path d="M77.5 0A77.5 77.5 0 0 1 132 132L77.5 188 23 132A77.5 77.5 0 0 1 77.5 0z" fill="url(#pg)"/><g fill="none" stroke="#fff" stroke-width="3"><circle cx="77" cy="48" r="6"/><path d="M70 60h14v20H70zM60 78h34M77 88v20M77 88l-20 18M77 88l20 18M42 72l10-6v12zM112 72l-10-6v12z"/></g></svg>
  <h3>MANAGED SERVICES</h3>
  <p>Sed ut perspiciatis unde omnis iste natus<br>error sit voluptatem accusantium dolorem<br>laudantium, totam rem aperiam</p>
  <div class="btn outline-btn">READ MORE</div>
</div>
<div class="abs service" style="left:764px;top:1035px">
  <svg class="pin" viewBox="0 0 155 190"><path d="M77.5 0A77.5 77.5 0 0 1 132 132L77.5 188 23 132A77.5 77.5 0 0 1 77.5 0z" fill="url(#pg)"/><g fill="none" stroke="#fff" stroke-width="3"><circle cx="72" cy="74" r="30"/><circle cx="72" cy="74" r="16"/><circle cx="72" cy="74" r="6"/><path d="M94 96l20 20"/></g></svg>
  <h3>OPTIMISE</h3>
  <p>Sed ut perspiciatis unde omnis iste natus<br>error sit voluptatem accusantium dolorem<br>laudantium, totam rem aperiam</p>
  <div class="btn outline-btn">READ MORE</div>
</div>

<section class="abs resources"></section>
<h2 class="abs sec-title" style="top:1553px;color:#fff">RESOURCES</h2>
<div class="abs rule" style="top:1600px;background:#fff"></div>
<p class="abs res-text">Sed ut perspiciatis unde omnis iste natus error sit voluptatem accusantium doloremque laudantium,<br>totam rem aperiam, eaque ipsa quae ab illo inventore veritatis</p>

<div class="abs card" style="left:112px;top:1735px"><svg width="52" height="50" viewBox="0 0 52 50" fill="none" stroke="#0455a3" stroke-width="2"><rect x="14" y="4" width="34" height="42"/><path d="M6 16h8v30H10a4 4 0 0 1-4-4zM20 22h22M20 28h22M20 34h22M20 40h14"/></svg>NEWS</div>
<div class="abs card" style="left:278px;top:1779px"><svg width="62" height="62" viewBox="0 0 62 62" fill="none" stroke="#0455a3" stroke-width="2"><circle cx="31" cy="31" r="28"/><circle cx="31" cy="31" r="22"/><circle cx="20" cy="26" r="4"/><circle cx="31" cy="26" r="4"/><circle cx="42" cy="26" r="4"/><path d="M14 40h34"/></svg>RESOURCES</div>
<div class="abs card" style="left:443px;top:1735px"><svg width="58" height="54" viewBox="0 0 58 54" fill="none" stroke="#0455a3" stroke-width="2"><rect x="3" y="6" width="52" height="45" rx="2"/><path d="M3 16h52M15 2v8M43 2v8M12 26h6M26 26h6M40 26h6M12 36h6M26 36l3 3 5-6M40 36h6"/></svg>EVENTS</div>
<div class="abs card" style="left:608px;top:1779px"><svg width="58" height="58" viewBox="0 0 58 58" fill="none" stroke="#0455a3" stroke-width="2"><rect x="8" y="3" width="42" height="28" rx="2"/><path d="M25 10l10 7-10 7z"/><circle cx="13" cy="40" r="4"/><circle cx="29" cy="40" r="4"/><circle cx="45" cy="40" r="4"/><path d="M5 55v-5a8 8 0 0 1 16 0v5M21 55v-5a8 8 0 0 1 16 0v5M37 55v-5a8 8 0 0 1 16 0v5"/></svg>WEBINARS</div>
<div class="abs card" style="left:772px;top:1735px"><svg width="62" height="60" viewBox="0 0 62 60" fill="none" stroke="#0455a3" stroke-width="3"><path d="M6 38h10v20H6zM24 28h10v30H24zM42 14h10v44H42zM36 8l11-6 11 6"/></svg><span style="font-size:15px">NOT FOR PROFIT</span></div>
<div class="abs card" style="left:938px;top:1779px"><svg width="62" height="58" viewBox="0 0 62 58" fill="none" stroke="#0455a3" stroke-width="2"><rect x="3" y="3" width="50" height="36"/><path d="M3 10h50"/><circle cx="30" cy="30" r="11"/><path d="M38 38l14 14"/></svg>CASE STUDIES</div>

<div class="abs btn support">SUPPORT</div>
<div class="abs btn incident">INCIDENT</div>

<h2 class="abs why-title">WHY <span>VORPLEXA?</span></h2>
<div class="abs why-block">
  <p class="why-text">Sed ut perspiciatis unde omnis iste natus error sit voluptatem accusantium doloremque laudantium, totam rem aperiam, eaque ipsa quae ab illo inventore veritatis et quasi architecto beatae vitae dicta sunt explicabo. Nemo enim ipsam voluptatem quia voluptas sit aspernatur aut odit aut fugit, sed quia consequuntur magni dolores eos qui ratione voluptatem sequi nesciunt. Neque porro quisquam est, qui dolorem ipsum quia dolor sit amet, consectetur, adipisci velit, sed quia non numquam eius modi</p>
  <div class="btn why-btn">READ MORE</div>
</div>
<div class="abs why-art" role="img" aria-label="Illustration of people working on laptops beside large light blue location pins and paper planes"></div>

<section class="abs partner"></section>
<div class="abs badge"></div>
<div class="abs badge-mark" role="img" aria-label="Quorvane Tellix Partner badge"></div>
<h3 class="abs partner-title">SED UT PERSPICIATIS UNDE OMNIS</h3>
<p class="abs partner-text">Nemo enim ipsam voluptatem quia voluptas sit aspernatur aut odit aut fugit, sed quia conse quuntur magni dolores eos qui ratione voluptatem sequi nesciunt. &nbsp;Neque porro quisquam est, qui dolorem ipsum quia dolor sit amet, consectetur, adipisci velit, sed</p>
<div class="abs btn partner-btn">LEARN MORE</div>

<footer class="abs footer"></footer>
<div class="abs f-brand mont" style="color:#fff"><div class="f-dot"></div><div class="f-name">VORPLEXA</div><div class="f-tag">EFFECTIVE TECHNOLOGY MANAGEMENT</div></div>
<div class="abs divider" style="left:446px"></div>
<div class="abs divider" style="left:777px"></div>

<svg class="abs" style="left:490px;top:3174px" width="20" height="26" viewBox="0 0 20 26" fill="none" stroke="#fff" stroke-width="1.6"><path d="M10 25s8-9 8-15a8 8 0 0 0-16 0c0 6 8 15 8 15z"/><circle cx="10" cy="10" r="3"/></svg>
<div class="abs f-info mont" style="left:530px;top:3166px;color:#fff">Address<br>P.O. Box 512 Sample Lane<br>Demo Town 04812</div>
<div class="abs social" style="left:530px;top:3248px"></div>
<div class="abs social" style="left:583px;top:3248px"></div>

<svg class="abs" style="left:828px;top:3178px" width="22" height="22" viewBox="0 0 24 24" fill="none" stroke="#fff" stroke-width="1.5"><path d="M6.6 10.8a15 15 0 006.6 6.6l2.2-2.2a1 1 0 011-.25 11.4 11.4 0 003.6.57 1 1 0 011 1V20a1 1 0 01-1 1A17 17 0 013 4a1 1 0 011-1h3.5a1 1 0 011 1c0 1.25.2 2.45.57 3.6a1 1 0 01-.25 1z"/></svg>
<div class="abs f-info mont" style="left:867px;top:3166px;color:#fff">Phone:<br>000-555-0187</div>
<svg class="abs" style="left:829px;top:3260px" width="22" height="16" viewBox="0 0 22 16" fill="none" stroke="#fff" stroke-width="1.5"><rect x="1" y="1" width="20" height="14"/><path d="M1 1l10 8 10-8"/></svg>
<div class="abs f-info mont" style="left:870px;top:3244px;color:#fff">Email:<br>hello@vorplexa.example</div>

<div class="abs f-rule"></div>
<nav class="abs f-nav mont" style="color:#fff"><span>HOME</span><span>CLOUD SAFELY</span><span>WHAT WE DO</span><span>RESOURCES</span><span>COMPANY</span><span>CONTACT US</span></nav>
<p class="abs copy mont" style="color:#fff">Vorplexa © 2021.All Rights Reserved.</p>

</body>
</html>
```